Private Dining Restaurant Menu Design

Looking for help in designing a private dining room menu brochure - probably would need 4 panel layout to make all of the content fit, or a 5.5x8" booklet. Open to your ideas on layout/vessel - would want to post on website and be able to print to hand out to guests interested in booking our private dining room.

All content is in the attached "Private Dining Menu".

Would like to match existing dinner menu design - also attached.

Website is www.copperkettlebistro.com

Requirements
Must have
• Easy to read format of a brochure of the private dining menu content - want to be able to hand out to interested guests and have it simple and easy to read/flip through.

```html
<!DOCTYPE html>
<html lang="en">
<head>
<meta charset="utf-8">
<title>Private Dining Room Menu</title>
<link href="https://fonts.googleapis.com/css2?family=Righteous&family=Tinos:ital,wght@0,400;0,700;1,400&display=swap" rel="stylesheet">
<style>
  :root {
    --bg: #1a1a1a;
    --bg-edge: #0d0d0d;
    --gold: #d4a72c;
    --text: #f2f2f2;
    --muted: #d8d8d8;
  }
  * { box-sizing: border-box; margin: 0; padding: 0; }
  html, body { width: 851px; height: 1200px; overflow: hidden; background: var(--bg-edge); }
  .menu-page {
    position: relative;
    width: 851px;
    height: 1200px;
    background: radial-gradient(ellipse at center, #262626 0%, var(--bg) 60%, var(--bg-edge) 100%);
    font-family: "Tinos", "Times New Roman", serif;
    color: var(--text);
    overflow: hidden;
  }
  .page-frame { position: absolute; inset: 0; }
  .menu-title {
    position: absolute;
    top: 66px; left: 0; right: 0;
    text-align: center;
    font-family: "Righteous", sans-serif;
    font-size: 64px;
    font-weight: 400;
    letter-spacing: 3px;
    color: var(--gold);
  }
  .room-title {
    position: absolute;
    top: 194px; left: 0; right: 0;
    text-align: center;
    font-family: "Righteous", sans-serif;
    font-size: 40px;
    font-weight: 400;
    letter-spacing: 2px;
    color: var(--gold);
  }
  .section { position: absolute; left: 80px; right: 80px; }
  .section-appetizers { top: 265px; }
  .section-platters { top: 475px; }
  .section-desserts { top: 677px; }
  .section-beverages { top: 830px; }
  .section-heading {
    font-size: 20px;
    line-height: 26px;
    font-weight: 700;
    text-transform: uppercase;
    margin-bottom: 14px;
  }
  .section-heading .note {
    font-size: 14px;
    font-weight: 400;
    font-style: italic;
    text-transform: none;
  }
  .item-list { list-style: none; }
  .menu-item {
    display: flex;
    align-items: baseline;
    font-size: 14.5px;
    line-height: 24px;
  }
  .menu-item .leader {
    flex: 1;
    border-bottom: 1px dotted var(--muted);
    margin: 0 4px;
    transform: translateY(-3px);
  }
  .menu-item .price { white-space: nowrap; }
  .section-beverages .section-heading { margin-bottom: 8px; }
  .beverage-intro {
    max-width: 560px;
    font-size: 14.5px;
    font-style: italic;
    line-height: 21px;
    margin-bottom: 18px;
  }
  .beverage-option {
    max-width: 640px;
    font-size: 14.5px;
    line-height: 21px;
    margin-bottom: 24px;
  }
  .beverage-option strong { font-weight: 700; }
</style>
</head>
<body>
<main class="menu-page">
  <svg class="page-frame" width="851" height="1200" viewBox="0 0 851 1200" aria-hidden="true">
    <g fill="none" stroke="var(--gold)">
      <path stroke-width="2.5" d="M60 18 H791 L833 60 V1140 L791 1182 H60 L18 1140 V60 Z"/>
      <path stroke-width="1" d="M66 28 H785 L823 66 V1134 L785 1172 H66 L28 1134 V66 Z"/>
    </g>
  </svg>

  <h1 class="menu-title">MENU</h1>
  <h2 class="room-title">PRIVATE DINING ROOM</h2>

  <section class="section section-appetizers">
    <h3 class="section-heading">Appetizers <span class="note">(price is by the dozen)</span></h3>
    <ul class="item-list">
      <li class="menu-item"><span>Texas Egg Rolls</span><span class="leader"></span><span class="price">$25</span></li>
      <li class="menu-item"><span>Chicken Wings (Buffalo, BBQ, OR Blackened)</span><span class="leader"></span><span class="price">$12</span></li>
      <li class="menu-item"><span>Baby Back Ribs</span><span class="leader"></span><span class="price">$30</span></li>
      <li class="menu-item"><span>Sliders (Pulled Pork or Rotisserie Chicken)</span><span class="leader"></span><span class="price">$35</span></li>
      <li class="menu-item"><span>Wood-Roasted Quesadillas</span><span class="leader"></span><span class="price">$30</span></li>
      <li class="menu-item"><span>Kettle Skins</span><span class="leader"></span><span class="price">$25</span></li>
    </ul>
  </section>

  <section class="section section-platters">
    <h3 class="section-heading">Platters – Small &amp; Large <span class="note">(small serves ~10-15 – large serves ~25-30)</span></h3>
    <ul class="item-list">
      <li class="menu-item"><span>Chips, Salsa, and Guacamole</span><span class="leader"></span><span class="price">sm$25/lg$45</span></li>
      <li class="menu-item"><span>Fresh Fruit Platter</span><span class="leader"></span><span class="price">sm$50/lg$75</span></li>
      <li class="menu-item"><span>Hot Artichoke Dip (comes with bread and tortilla chips)</span><span class="leader"></span><span class="price">sm$30/lg$60</span></li>
      <li class="menu-item"><span>Domestic Cheese and Crackers</span><span class="leader"></span><span class="price">sm$45/lg$65</span></li>
      <li class="menu-item"><span>Fresh Veggie Platter</span><span class="leader"></span><span class="price">sm$40/lg$65</span></li>
    </ul>
  </section>

  <section class="section section-desserts">
    <h3 class="section-heading">Dessert Options <span class="note">(Price is per item)</span></h3>
    <ul class="item-list">
      <li class="menu-item"><span>House Made Cheesecake Slice (turtle, strawberry, or plain)</span><span class="leader"></span><span class="price">$5/slice</span></li>
      <li class="menu-item"><span>Whole House Made Cheesecake (turtle, strawberry, or plain)</span><span class="leader"></span><span class="price">$60 (15 slices at $4/slice)</span></li>
      <li class="menu-item"><span>Assorted Bars and Cookie Platter (25 bars/cookies)</span><span class="leader"></span><span class="price">$25</span></li>
    </ul>
  </section>

  <section class="section section-beverages">
    <h3 class="section-heading">Beverage Options</h3>
    <p class="beverage-intro">We offer a full bar with a variety of NA, liquor, beer, and wine options All beverages will be charged per menu price</p>
    <p class="beverage-option"><strong>NA Beverage Host</strong>: Soda, Iced Tea, Lemonade, Coffee, and Hot Tea hosted by renter for their guests</p>
    <p class="beverage-option"><strong>Full Host</strong>: All NA and Alcoholic beverages to be hosted by the renter for their guests</p>
    <p class="beverage-option"><strong>Partial Host</strong>: A set amount or certain types of beverages hosted by the renter for their guests</p>
    <p class="beverage-option"><strong>Cash Bar</strong>: Each beverage will be paid for by each individual guest</p>
  </section>
</main>
</body>
</html>
```